Carpet cleaning company focused on high quality needs business cards

We are a growing company that just merged with another company and need to design a new business card. We do both residential as well as commercial cleaning. We do carpet, tile & grout, upholstery, hard floors, and stain & pet odor removal. We treat our customers like family and strive to achieve outstanding results with every job.

```html
<!DOCTYPE html>
<html lang="en">
<head>
<meta charset="utf-8">
<title>Brightwell Carpet Care – Business Cards</title>
<link rel="stylesheet" href="https://fonts.googleapis.com/css2?family=Open+Sans:wght@400;600&display=swap">
<style>
  :root {
    --backdrop: #bdbdbd;
    --card: #ffffff;
    --ink: #111111;
    --accent-red: #e8453c;
    --accent-blue: #1a84c6;
    --rule: #333333;
  }
  * { box-sizing: border-box; margin: 0; padding: 0; }
  html, body { width: 1200px; height: 780px; overflow: hidden; }
  body {
    background: var(--backdrop);
    font-family: "Open Sans", Arial, sans-serif;
    color: var(--ink);
    position: relative;
  }
  .card {
    position: absolute;
    width: 520px;
    height: 300px;
    background: var(--card);
    box-shadow: 0 6px 18px rgba(0,0,0,0.25);
  }
  .card--details { left: 50px; top: 240px; display: flex; }
  .card--brand { left: 630px; top: 240px; display: flex; align-items: center; justify-content: center; }

  .brand { display: flex; align-items: center; gap: 12px; }
  .brand__dot { background: var(--accent-blue); border-radius: 50%; flex: none; }
  .brand__name { font-weight: 600; line-height: 1.2; color: var(--ink); white-space: nowrap; }

  .card--details .brand__dot { width: 14px; height: 14px; }
  .card--details .brand__name { font-size: 18px; }
  .card--brand .brand__dot { width: 22px; height: 22px; }
  .card--brand .brand__name { font-size: 30px; }

  .details__brand-side {
    width: 250px;
    display: flex; align-items: center; justify-content: center;
    border-right: 1px solid var(--rule);
    margin: 60px 0;
  }
  .details__info { padding: 52px 0 0 30px; }
  .person__name { font-size: 27px; font-weight: 600; line-height: 1.1; }
  .person__first { color: var(--accent-red); }
  .person__last { color: var(--accent-blue); }
  .person__title { font-size: 13px; margin-bottom: 16px; }
  .address { font-size: 12.5px; line-height: 1.45; margin-bottom: 14px; font-style: normal; }
  .contact { list-style: none; font-size: 12.5px; line-height: 1.6; }
  .contact li { display: flex; align-items: center; gap: 8px; }
  .contact svg { width: 12px; height: 12px; flex: none; }
</style>
</head>
<body>

<section class="card card--details" aria-label="Business card, contact side">
  <div class="details__brand-side">
    <div class="brand">
      <span class="brand__dot" aria-hidden="true"></span>
      <span class="brand__name">Brightwell Carpet Care</span>
    </div>
  </div>
  <div class="details__info">
    <h1 class="person__name"><span class="person__first">Marta</span> <span class="person__last">Novakova</span></h1>
    <p class="person__title">Managing Director</p>
    <address class="address">418 Linden Ave. Suite 120<br>Maple Falls, TX 75001</address>
    <ul class="contact">
      <li>
        <svg viewBox="0 0 12 12" aria-hidden="true"><path d="M2.5 1l2 2.2-1 1.3a6 6 0 0 0 4 4l1.3-1 2.2 2-1 1.5C5 11 1 7 1 2.5z" fill="var(--accent-red)"/></svg>
        (555) 014-2290
      </li>
      <li>
        <svg viewBox="0 0 12 12" aria-hidden="true"><rect x="1" y="2.5" width="10" height="7" fill="var(--accent-red)"/><path d="M1 2.5l5 4 5-4" stroke="#fff" fill="none"/></svg>
        info@example.com
      </li>
      <li>
        <svg viewBox="0 0 12 12" aria-hidden="true"><circle cx="6" cy="6" r="5" fill="var(--accent-red)"/><path d="M1 6h10M6 1c-2.5 3-2.5 7 0 10M6 1c2.5 3 2.5 7 0 10" stroke="#fff" stroke-width="0.7" fill="none"/></svg>
        www.example.com
      </li>
    </ul>
  </div>
</section>

<section class="card card--brand" aria-label="Business card, brand side">
  <div class="brand">
    <span class="brand__dot" aria-hidden="true"></span>
    <span class="brand__name">Brightwell Carpet Care</span>
  </div>
</section>

</body>
</html>
```